Company brochure for our unique consulting business

We are a small consulting business offering a unique set of services to our clients.. In simple terms we are a business improvement consultancy helping our clients get the best out of their businesses. We work with clients across multiple sectors and deliver a variety of services. We want to put together a brochure to cover these main themes:1. Who we are2. What we do3. The type of people we employ4. The sectors we work inWhile the brochure needs to have a certain corporate feel to it, we don't want it to be "boring" or "stiff". We would like it to have a slightly "friendly" or "informal" feel to it, to reflect the type of organisation we are.We have a company website http://brevalconsultingpartners.net , however we do not want to directly replicate the content or feel as we recognise it needs updating.We would like the brochure to be A4 portrait format. We anticipate requiring 12 sides (including covers) but we are happy to be guided on this based on the content we have provided.The attached ppt file gives the detail of the content to be included and also shows the proposed pagination. For the front cover we would like to try 2 versions, one with the BCP logo and one with the Breval Consulting Partners logo (a file of both is attached)One of the most important pages will be the "Our Services" page. We would like this to cover the centre fold. In the ppt file we have shown an example layout, but this is where we need most help - we are clearly not graphic designers! This page will be the most used page in sales meetings etc.Also attached is the following:1. file for our BrevalConsulting Partners company logo.2. File for our BCP company logo3. Files for Derek's signatures (for under photos) - Owen's to follow4. Photo of Derek & Owen (person in purple shirt to be cropped out)Thank you and really excited to see what everyone comes back with.Derek & Owen

Target Market(s)

Very broad - Manufacturing, Healthcare, Hospitality

Industry/Entity Type

Management Consulting

Font styles to use
Other font styles liked:
• We use Swiss721, but happy to be guided by designer

Colors
3276b5
85abd2
0355a3
333333
5c5c5c
9d9d9d
d9d9d9

Requirements
Must have
• Corporate feel
Nice to have
• Slightly friendly feel
• Our standard "blue" is (CORRECTION) - R55 G96 B146 #376092 and our standard grey is R197 G178, B179 - #B3B2B2, which we would like to keep, but other colours we are happy to be guided on. Brand guidelines attached.

```html
<!DOCTYPE html>
<html lang="en">
<head>
<meta charset="utf-8">
<title>Our Values – BCP</title>
<link href="https://fonts.googleapis.com/css2?family=Arimo:wght@700&family=Open+Sans:wght@400&display=swap" rel="stylesheet">
<style>
  :root {
    --brand-blue: #2750d3;
    --stripe-blue: #2a5bc9;
    --footer-blue: #2b4fc2;
    --light-grey: #dcdddd;
    --strip-grey: #3e4146;
    --ink: #1a1a1a;
    --arrow-navy: #141b3b;
    --logo-ink: #1d1d1f;
    --white: #ffffff;
  }
  * { margin: 0; padding: 0; box-sizing: border-box; }
  html, body { width: 848px; height: 1200px; overflow: hidden; background: var(--white); }
  .page { position: relative; width: 848px; height: 1200px; overflow: hidden; background: var(--white); }
  .page-art { position: absolute; inset: 0; width: 848px; height: 1200px; }
  .brand-name {
    position: absolute; left: 70px; top: 34px;
    font-family: "Arimo", Arial, sans-serif; font-weight: 700;
    font-size: 36px; letter-spacing: 1px; color: var(--logo-ink);
  }
  .page-title {
    position: absolute; left: 390px; top: 72px;
    font-family: "Arimo", Arial, sans-serif; font-weight: 700;
    font-size: 32px; color: var(--white);
  }
  .values-list { position: absolute; left: 158px; top: 538px; width: 572px; list-style: none; }
  .value-item {
    position: absolute; left: 0; width: 572px;
    display: flex; align-items: flex-start;
  }
  .value-arrow { flex: 0 0 27px; width: 27px; height: 29px; margin-right: 10px; margin-top: 1px; }
  .value-text {
    flex: 1; font-family: "Open Sans", Verdana, sans-serif; font-size: 15.5px;
    line-height: 25.6px; color: var(--ink); text-align: justify; letter-spacing: 0.2px;
  }
  .page-number {
    position: absolute; left: 50px; top: 1148px;
    font-family: "Open Sans", Verdana, sans-serif; font-size: 20px; color: var(--white);
  }
</style>
</head>
<body>
<div class="page">
  <svg class="page-art" viewBox="0 0 1060 1500" xmlns="http://www.w3.org/2000/svg">
    <defs>
      <linearGradient id="cityTones" x1="0" y1="0" x2="1" y2="1">
        <stop offset="0" stop-color="#cfd1d3"/>
        <stop offset="0.5" stop-color="#8d9094"/>
        <stop offset="1" stop-color="#4a4d52"/>
      </linearGradient>
      <radialGradient id="stoneTones" cx="0.55" cy="0.6" r="0.7">
        <stop offset="0" stop-color="#3b3d40"/>
        <stop offset="0.45" stop-color="#7c7f83"/>
        <stop offset="1" stop-color="#c9cbcd"/>
      </radialGradient>
    </defs>
    <polygon class="header-grey" points="0,0 320,0 425,122 0,122" fill="var(--light-grey)"/>
    <polygon class="header-blue" points="320,0 1060,0 1060,155 452,155" fill="var(--brand-blue)"/>
    <polygon class="header-rule" points="452,155 1060,155 1060,163 458,163" fill="var(--strip-grey)"/>
    <polygon class="photo-city" role="img" aria-label="Black and white photo looking up at office towers against the sky"
             points="0,122 425,122 458,163 0,800" fill="url(#cityTones)"/>
    <polygon class="accent-stripe" points="458,163 495,163 20,820 0,820 0,800" fill="var(--stripe-blue)"/>
    <polygon class="photo-stones" role="img" aria-label="Black and white photo of a balanced stack of flat stones"
             points="495,163 1060,163 1060,590 186,590" fill="url(#stoneTones)"/>
    <rect class="footer-band" x="0" y="1403" width="1060" height="97" fill="var(--footer-blue)"/>
  </svg>

  <div class="brand-name">BCP</div>
  <h1 class="page-title">Our Values</h1>

  <ul class="values-list">
    <li class="value-item" style="top:0">
      <svg class="value-arrow" viewBox="0 0 27 29"><polygon points="0,0 27,14.5 0,29" fill="var(--arrow-navy)"/></svg>
      <p class="value-text">Be TRUSTED by our team and clients, so that our opinions are sought and our recommendations valued.</p>
    </li>
    <li class="value-item" style="top:87px">
      <svg class="value-arrow" viewBox="0 0 27 29"><polygon points="0,0 27,14.5 0,29" fill="var(--arrow-navy)"/></svg>
      <p class="value-text">Have a tight knit relationship with our clients, so we are seen as a PARTNER and not just supplier.</p>
    </li>
    <li class="value-item" style="top:173px">
      <svg class="value-arrow" viewBox="0 0 27 29"><polygon points="0,0 27,14.5 0,29" fill="var(--arrow-navy)"/></svg>
      <p class="value-text">Be focused on return-on-investment, but predominantly, always deliver GREAT VALUE.</p>
    </li>
    <li class="value-item" style="top:266px">
      <svg class="value-arrow" viewBox="0 0 27 29"><polygon points="0,0 27,14.5 0,29" fill="var(--arrow-navy)"/></svg>
      <p class="value-text">DEVELOP &amp; INVEST IN our own people to continually stay one step ahead.</p>
    </li>
    <li class="value-item" style="top:365px">
      <svg class="value-arrow" viewBox="0 0 27 29"><polygon points="0,0 27,14.5 0,29" fill="var(--arrow-navy)"/></svg>
      <p class="value-text">Work relentlessly to deliver results for our clients, but ensure we collectively ENJOY THE JOURNEY.</p>
    </li>
    <li class="value-item" style="top:464px">
      <svg class="value-arrow" viewBox="0 0 27 29"><polygon points="0,0 27,14.5 0,29" fill="var(--arrow-navy)"/></svg>
      <p class="value-text">Take SOCIAL RESPONSIBILITY seriously by supporting other worthwhile organisations.</p>
    </li>
  </ul>

  <div class="page-number">2</div>
</div>
</body>
</html>
```